Kelmo website design on shopify

Job Description:
As a web designer for Kelmo, you will be the driving force behind designing and developing our new e-commerce website. Your responsibility will be to create an attractive, functional, and intuitive online shopping experience where customers can effortlessly discover and purchase high-quality supplements such as pre-workout, creatine, and protein shakes. Your design will play a crucial role in enhancing our brand and engaging our target audience.

```html
<!DOCTYPE html>
<html lang="en">
<head>
<meta charset="utf-8">
<title>Kelmo — Supplements</title>
<link href="https://fonts.googleapis.com/css2?family=Montserrat:wght@500;600;700&family=Roboto:wght@400;500&display=swap" rel="stylesheet">
<style>
  :root{
    --hero-purple:#c27bcf;
    --deep-purple:#7a2887;
    --accent:#6d2580;
    --ink:#1f1f1f;
    --muted:#444;
    --lavender:#efe6f1;
    --footer:#2b2b2b;
    --white:#fff;
  }
  *{box-sizing:border-box;margin:0;padding:0}
  html,body{width:1200px;height:4494px;overflow:hidden}
  body{position:relative;background:var(--white);font-family:'Roboto',sans-serif;color:var(--ink)}
  .abs{position:absolute}
  .heading{font-family:'Montserrat',sans-serif;font-weight:600;letter-spacing:.5px}
  .btn{position:absolute;display:flex;align-items:center;justify-content:center;border:2px solid var(--accent);color:var(--accent);font-family:'Montserrat',sans-serif;font-weight:700;font-size:15px;letter-spacing:.3px;background:transparent}
  .btn.light{border-color:var(--white);color:var(--white)}
  .photo{position:absolute}
  .brand{font-family:'Montserrat',sans-serif;font-weight:500;display:flex;align-items:center;gap:10px;line-height:1}
  .brand .dot{border-radius:50%;display:inline-block;flex:none}

  /* hero */
  .hero-panel{left:0;top:0;width:485px;height:686px;background:var(--hero-purple)}
  .hero-photo{left:485px;top:0;width:715px;height:686px;background:linear-gradient(160deg,#e9dccb 0%,#d8c3a6 55%,#8a6a4a 85%,#5b4330 100%)}
  .nav{left:110px;top:56px;display:flex;gap:26px;font-size:14px;color:var(--white)}
  .hero-welcome{left:110px;top:212px;font-family:'Montserrat',sans-serif;font-size:25px;color:var(--white);font-weight:500}
  .hero-title{left:108px;top:255px;font-family:'Montserrat',sans-serif;font-size:86px;font-weight:500;color:var(--white);letter-spacing:2px}
  .hero-text{left:110px;top:378px;width:330px;font-size:14px;line-height:29px;color:var(--white)}
  .hero-logo{left:546px;top:46px;color:var(--accent);font-size:36px}
  .icons{left:978px;top:55px;display:flex;gap:22px}

  .section-title{font-size:37px}
  .card-name{font-family:'Montserrat',sans-serif;font-weight:500;font-size:25px}
  .card-price{font-family:'Montserrat',sans-serif;font-weight:700;font-size:29px;color:var(--accent)}

  .about-panel{left:747px;top:1400px;width:453px;height:557px;background:var(--deep-purple)}
  .about-text{left:815px;top:1565px;width:280px;font-size:12.5px;line-height:22px;color:var(--white);text-align:justify}

  .quality-band{left:0;top:2827px;width:1200px;height:515px;background:var(--lavender)}
  .quality-text{left:136px;top:3016px;width:374px;font-size:13.5px;line-height:24px;color:var(--muted);text-align:justify}

  .blog-title{font-family:'Montserrat',sans-serif;font-weight:500;font-size:21px;line-height:30px;width:310px}
  .blog-text{font-size:12.5px;line-height:20px;color:var(--muted);width:310px}

  footer{position:absolute;left:0;top:4116px;width:1200px;height:378px;background:var(--footer);color:var(--white)}
  .f-head{font-family:'Montserrat',sans-serif;font-weight:600;font-size:17px}
  .f-links{font-size:15px;line-height:30px}
  .f-contact{font-size:15px;line-height:26px}
  .social{display:flex;gap:16px}
  .social span{width:38px;height:38px;border-radius:50%;background:var(--white);display:block}
</style>
</head>
<body>

<div class="abs hero-panel"></div>
<div class="photo hero-photo" role="img" aria-label="Two black supplement jars on a wooden shelf beside a potted plant"></div>
<nav class="abs nav"><span>Home</span><span>About Us</span><span>Products</span><span>Contact Us</span></nav>
<div class="abs hero-welcome">WELCOME TO</div>
<div class="abs hero-title">KELMO</div>
<p class="abs hero-text">Lorem ipsum dolor sit amet, consectetur adipiscing elit, sed do eiusmod</p>
<div class="btn light" style="left:110px;top:476px;width:132px;height:59px">SHOP NOW</div>
<div class="abs brand hero-logo"><span class="dot" style="width:36px;height:36px;background:var(--accent)"></span><span>KELMO</span></div>
<div class="abs icons">
  <svg width="18" height="18" viewBox="0 0 18 18"><circle cx="7.5" cy="7.5" r="5.5" fill="none" stroke="#fff" stroke-width="2.4"/><line x1="11.5" y1="11.5" x2="16.5" y2="16.5" stroke="#fff" stroke-width="2.6"/></svg>
  <svg width="16" height="18" viewBox="0 0 16 18"><circle cx="8" cy="5" r="4.3" fill="#fff"/><path d="M0 18c0-6 3.5-8 8-8s8 2 8 8z" fill="#fff"/></svg>
  <svg width="20" height="18" viewBox="0 0 20 18"><path d="M0 1h4l3 10h10l2-7H6" fill="none" stroke="#fff" stroke-width="2.2"/><circle cx="8" cy="15.5" r="2" fill="#fff"/><circle cx="16" cy="15.5" r="2" fill="#fff"/></svg>
</div>

<h2 class="abs heading section-title" style="left:113px;top:803px">BEST SELLERS</h2>
<div class="btn" style="left:956px;top:797px;width:132px;height:59px">VIEW ALL</div>
<div class="photo" style="left:112px;top:903px;width:307px;height:286px;background:linear-gradient(135deg,#8c7a66,#3b332c)" role="img" aria-label="Dumbbells and supplement tub on a gym floor"></div>
<div class="photo" style="left:447px;top:903px;width:307px;height:286px;background:linear-gradient(135deg,#6e6e6e,#2c2c2c)" role="img" aria-label="Creatine powder with capsules and a dumbbell"></div>
<div class="photo" style="left:781px;top:903px;width:307px;height:286px;background:linear-gradient(135deg,#3a3a3a,#1a1a1a)" role="img" aria-label="Scoop of protein powder poured into a shaker"></div>
<div class="abs card-name" style="left:110px;top:1212px">Pre-workout</div>
<div class="abs card-price" style="left:110px;top:1256px">$50</div>
<div class="abs card-name" style="left:445px;top:1212px">Creatine</div>
<div class="abs card-price" style="left:445px;top:1256px">$50</div>
<div class="abs card-name" style="left:780px;top:1212px">Protein shakes</div>
<div class="abs card-price" style="left:780px;top:1256px">$50</div>

<div class="photo" style="left:0;top:1400px;width:747px;height:557px;background:linear-gradient(135deg,#2f4a52,#15222a 60%,#0e1418)" role="img" aria-label="Athlete seated on a gym bench mixing a supplement drink"></div>
<div class="abs about-panel"></div>
<h2 class="abs heading section-title" style="left:815px;top:1484px;color:var(--white)">ABOUT US</h2>
<p class="abs about-text">Lorem ipsum dolor sit amet, consectetur adipiscing elit, sed do eiusmod tempor incididunt ut labore et dolore magna aliqua. Ut enim ad minim veniam, quis nostrud exercitation ullamco laboris nisi ut aliquip ex ea commodo consequat. Duis aute irure dolor in reprehenderit in voluptate velit esse cillum dolore eu fugiat nulla pariatur. Excepteur sint occaecat cupidatat non proident, sunt in culpa qui officia deserunt mollit</p>
<div class="btn light" style="left:815px;top:1807px;width:132px;height:58px">SHOP NOW</div>

<h2 class="abs heading section-title" style="left:0;width:1200px;text-align:center;top:2058px">OUR PRODUCTS</h2>
<div class="photo" style="left:150px;top:2175px;width:359px;height:344px;background:linear-gradient(160deg,#4a4a4a,#262626)" role="img" aria-label="Black supplement bottle against a dark stone wall"></div>
<div class="abs card-name" style="left:150px;width:359px;text-align:center;top:2552px">Pre-workout</div>
<div class="abs card-price" style="left:150px;width:359px;text-align:center;top:2596px">$50</div>
<div class="btn" style="left:249px;top:2656px;width:159px;height:59px">ADD TO CART</div>
<div class="photo" style="left:616px;top:2178px;width:472px;height:454px;background:linear-gradient(150deg,#2c2c3c,#14141c)" role="img" aria-label="Protein tub, shaker with a milky drink and capsules"></div>

<div class="abs quality-band"></div>
<h2 class="abs heading" style="left:136px;top:2890px;font-size:37px;line-height:51px">HIGH-QUALITY<br>SUPPLEMENTS</h2>
<p class="abs quality-text">Lorem ipsum dolor sit amet, consectetur adipiscing elit, sed do eiusmod tempor incididunt ut labore et dolore magna aliqua. Ut enim ad minim veniam, quis nostrud exercitation ullamco laboris nisi ut aliquip ex ea commodo consequat. Duis aute irure dolor in reprehenderit in voluptate velit esse cillum dolore eu fugiat nulla pariatur. Excepteur sint occaecat cupidatat non proident, sunt in culpa qui officia deserunt mollit</p>
<div class="btn" style="left:136px;top:3211px;width:131px;height:59px">SHOP NOW</div>
<div class="photo" style="left:621px;top:2916px;width:408px;height:338px;border:2px solid var(--accent);background:linear-gradient(135deg,#eceae6,#c9c4bc)" role="img" aria-label="Man drinking from a shaker in a bright kitchen"></div>

<h2 class="abs heading section-title" style="left:113px;top:3460px">BLOG ARTICLES</h2>
<div class="btn" style="left:956px;top:3453px;width:132px;height:59px">VIEW ALL</div>
<div class="photo" style="left:112px;top:3561px;width:307px;height:285px;background:linear-gradient(135deg,#4a2a2a,#141414)" role="img" aria-label="Hands holding a black shaker bottle"></div>
<div class="photo" style="left:447px;top:3561px;width:307px;height:285px;background:linear-gradient(135deg,#9fb0b8,#3a3f4a)" role="img" aria-label="Man in a gym drinking from a pink shaker"></div>
<div class="photo" style="left:780px;top:3561px;width:307px;height:285px;background:linear-gradient(135deg,#9a9a9a,#5a5a5a)" role="img" aria-label="Pouring protein powder into a clear shaker"></div>
<div class="abs blog-title" style="left:110px;top:3872px">Lorem ipsum dolor sit amet, consectetur adipiscing</div>
<p class="abs blog-text" style="left:110px;top:3944px">Lorem ipsum dolor sit amet, consectetur adipiscing elit, sed do eiusmod tempor incididunt ut labore et dolore magna aliqua. Ut enim ad minim</p>
<div class="abs blog-title" style="left:445px;top:3872px">Lorem ipsum dolor sit amet, consectetur adipiscing</div>
<p class="abs blog-text" style="left:445px;top:3944px">Lorem ipsum dolor sit amet, consectetur adipiscing elit, sed do eiusmod tempor incididunt ut labore et dolore magna aliqua. Ut enim ad minim</p>
<div class="abs blog-title" style="left:778px;top:3872px">Lorem ipsum dolor sit amet, consectetur adipiscing</div>
<p class="abs blog-text" style="left:778px;top:3944px">Lorem ipsum dolor sit amet, consectetur adipiscing elit, sed do eiusmod tempor incididunt ut labore et dolore magna aliqua. Ut enim ad minim</p>

<footer>
  <div class="abs brand" style="left:113px;top:126px;font-size:44px;color:var(--white)"><span class="dot" style="width:52px;height:52px;background:var(--accent)"></span><span>KELMO</span></div>
  <div class="abs social" style="left:112px;top:230px"><span></span><span></span><span></span><span></span></div>

  <div class="abs f-head" style="left:445px;top:95px">QUICK LINKS</div>
  <div class="abs f-links" style="left:445px;top:128px">Home<br>About Us<br>Products<br>Bestsellers<br>Contact Us</div>

  <div class="abs f-head" style="left:621px;top:95px">CONTACT US</div>
  <svg class="abs" style="left:621px;top:138px" width="16" height="20" viewBox="0 0 16 20"><path d="M8 0a7 7 0 0 1 7 7c0 5-7 13-7 13S1 12 1 7a7 7 0 0 1 7-7z" fill="#fff"/><circle cx="8" cy="7" r="2.6" fill="#2b2b2b"/></svg>
  <div class="abs f-contact" style="left:653px;top:132px;width:180px">147 Lorem ipsum dolor sit amet, consectetur</div>
  <svg class="abs" style="left:621px;top:208px" width="17" height="17" viewBox="0 0 17 17"><path d="M3 0l4 4-2 3c1 2 3 4 5 5l3-2 4 4-3 3C7 17 0 10 0 3z" fill="#fff"/></svg>
  <div class="abs f-contact" style="left:653px;top:203px">+1 (888) 888 8888</div>
  <svg class="abs" style="left:621px;top:244px" width="18" height="13" viewBox="0 0 18 13"><rect width="18" height="13" fill="#fff"/><path d="M0 0l9 7 9-7" fill="none" stroke="#2b2b2b" stroke-width="1.6"/></svg>
  <div class="abs f-contact" style="left:653px;top:237px">info@kelmo.com</div>

  <div class="abs f-head" style="left:862px;top:95px">NEWSLETTER</div>
  <div class="abs" style="left:862px;top:145px;width:226px;height:40px;background:var(--white);display:flex;align-items:center;padding-left:14px;font-size:14px;color:#888">Ener email</div>
  <div class="abs" style="left:1034px;top:145px;width:54px;height:40px;background:var(--accent);border-radius:4px;display:flex;align-items:center;justify-content:center">
    <svg width="16" height="12" viewBox="0 0 16 12"><rect width="16" height="12" fill="#fff"/><path d="M0 0l8 6 8-6" fill="none" stroke="#6d2580" stroke-width="1.6"/></svg>
  </div>

  <div class="abs" style="left:0;width:1200px;text-align:center;top:330px;font-size:14px">©Copyrights 2023 Kelmo &nbsp;&nbsp;|&nbsp;&nbsp; All Rights Reserved</div>
</footer>

</body>
</html>
```